Sell the dream! Property investment proposal document

We are looking for a proposal document which outlines our vision for property development. The purpose of the document is to raise investment from investors - sell the dream!
Brief summary:
Kestrel Dwellings Developments, is an emerging New Zealand property investment company with a focus on providing unique property investment opportunities.
Our expertise and capabilities in architectural modular homes provide us with a remarkable advantage in tackling the development of properties that are typically considered challenging, remote, or uniquely positioned.
Our specialization in this niche sector of property development not only sets us apart from competitors, but also paves the way for lucrative investment opportunities in the New Zealand property market.
Feel free to use any images from www.kestreldwellings.co.nz
Target Market(s)
investors for a unique property development opportunity
Industry/Entity Type
luxury property development in unique locations throughout New Zealand
Colors
Designer to choose only greyscale colors for use in the design.
Look and feel

```html
<!DOCTYPE html>
<html lang="en">
<head>
<meta charset="utf-8">
<title>Kestrel Dwellings – Investment Proposal</title>
<link rel="stylesheet" href="https://fonts.googleapis.com/css2?family=Montserrat:wght@300;400;500;700&family=Roboto:wght@400;500&display=swap">
<style>
:root{
  --stage:#ededed;
  --paper:#ffffff;
  --ink:#111111;
  --text:#2b2b2b;
  --soft:#f3f3f3;
  --mid:#a9a9a9;
  --light:#cfcfcf;
}
*{margin:0;padding:0;box-sizing:border-box}
html,body{width:1200px;height:544px;overflow:hidden;background:var(--stage)}
body{position:relative;font-family:'Roboto',sans-serif;color:var(--text)}
.page{position:absolute;top:53px;width:339px;height:439px;background:var(--paper);box-shadow:0 2px 6px rgba(0,0,0,.12);overflow:hidden}
.page--cover{left:52px}
.page--overview{left:430px}
.page--origins{left:809px}

.brand{font-family:'Montserrat',sans-serif;font-weight:500;color:var(--ink);letter-spacing:-1.5px;line-height:1;position:absolute}

/* cover */
.cover-photo{position:absolute;left:0;top:0;width:339px;height:270px;
  background:linear-gradient(160deg,#e9d9c0 0%,#b9c28f 28%,#7f9a5a 45%,#a88e6c 62%,#cdbfae 80%,#e4dcd4 100%);
  clip-path:polygon(0 0,100% 0,100% 201px,254px 265px,0 201px)}
.cover-edge{position:absolute;left:0;top:0}
.cover .brand{left:18px;top:248px;font-size:40px}
.cover-title{position:absolute;left:0;right:0;top:318px;text-align:center;font-family:'Montserrat',sans-serif;color:var(--ink);line-height:1.15}
.cover-title strong{display:block;font-weight:700;font-size:14px}
.cover-title span{display:block;font-weight:300;font-size:14px;letter-spacing:.3px}
.cover-lede{position:absolute;left:30px;right:30px;top:357px;text-align:center;font-size:6.4px;line-height:9.4px}

/* headers */
.page-head{position:absolute;left:0;top:0}
.page .head-brand{left:19px;top:10px;font-size:34px}
.page-title{position:absolute;right:19px;top:18px;font-family:'Montserrat',sans-serif;color:#fff;font-size:12.5px;letter-spacing:.4px}
.page-title b{font-weight:700}
.page-title span{font-weight:300}

.copy{position:absolute;left:28px;right:28px;text-align:center;font-size:6.6px;line-height:9.7px}
.copy p{margin-bottom:6px}
.page--overview .copy{top:77px}
.page--origins .copy{top:241px;left:30px;right:30px}

.photo{position:absolute}
.photo--villa{left:32px;top:281px;width:143px;height:96px;background:linear-gradient(180deg,#c9cfd6 0%,#b7bfc6 40%,#4a4e4a 58%,#6d7b55 80%,#55683f 100%)}
.photo--facade{left:163px;top:298px;width:145px;height:96px;background:linear-gradient(180deg,#bcc2c8 0%,#8d9190 35%,#2b2d2d 60%,#5d6a52 82%,#b9bbb8 100%);border-left:3px solid var(--paper)}
.photo--meeting{left:43px;top:81px;width:232px;height:143px;background:linear-gradient(135deg,#b7c1b6 0%,#55625a 35%,#1f2730 60%,#30343a 80%,#8b8e92 100%)}
.bracket{position:absolute;left:0;top:0}

.page-foot{position:absolute;left:0;bottom:0;width:339px;height:16px}
.foot-svg{position:absolute;left:0;top:0}
.foot-item{position:absolute;top:0;height:16px;display:flex;align-items:center;gap:4px;color:#fff;font-size:3.8px}
.foot-item--phone{left:20px}
.foot-item--mail{left:64px}
.foot-icon{width:10px;height:10px;border-radius:50%;background:#fff;display:flex;align-items:center;justify-content:center}
.page-no{position:absolute;right:19px;top:0;line-height:16px;font-family:'Montserrat',sans-serif;font-size:3.9px;letter-spacing:1px;color:#fff}
</style>
</head>
<body>

<!-- cover -->
<section class="page page--cover cover">
  <div class="cover-photo" role="img" aria-label="Hand placing a small wooden house on stacked coins with seedlings growing"></div>
  <svg class="cover-edge" width="339" height="340" viewBox="0 0 339 340">
    <polyline points="90,227 254,279 318,228" fill="none" stroke="var(--light)" stroke-width="3"/>
  </svg>
  <div class="brand">Kestrel</div>
  <h1 class="cover-title"><strong>MODULAR</strong><span>ARCHITECTURAL HOMES</span></h1>
  <p class="cover-lede">Architecturally-designed, highly customisable homes, built off-site, delivered to and connected on your own, personal plot of land anywhere in New Zealand.</p>
  <footer class="page-foot">
    <svg class="foot-svg" width="339" height="16"><rect width="339" height="16" fill="var(--ink)"/><polygon points="274,0 339,0 339,16 262,16" fill="var(--mid)"/><polygon points="270,0 274,0 262,16 258,16" fill="var(--paper)"/></svg>
    <div class="foot-item foot-item--phone"><span class="foot-icon"><svg width="6" height="6" viewBox="0 0 24 24"><path fill="#111" d="M6.6 10.8a15 15 0 006.6 6.6l2.2-2.2c.3-.3.7-.4 1-.2 1.1.4 2.3.6 3.6.6.6 0 1 .4 1 1V20c0 .6-.4 1-1 1A17 17 0 013 4c0-.6.4-1 1-1h3.5c.6 0 1 .4 1 1 0 1.3.2 2.5.6 3.6.1.3 0 .7-.2 1z"/></svg></span>09 555 0142</div>
    <div class="foot-item foot-item--mail"><span class="foot-icon"><svg width="6" height="6" viewBox="0 0 24 24"><path fill="#111" d="M3 5h18v14H3z"/><path fill="none" stroke="#fff" stroke-width="2" d="M3 6l9 7 9-7"/></svg></span>sales@kestreldwellings.co.nz</div>
    <div class="page-no">PAGE NO 01</div>
  </footer>
</section>

<!-- business overview -->
<section class="page page--overview">
  <svg class="page-head" width="339" height="62" viewBox="0 0 339 62">
    <rect width="339" height="54" fill="var(--soft)"/>
    <polygon points="104,0 112,0 158,54 150,54" fill="var(--light)"/>
    <polygon points="112,0 339,0 339,47 152,47" fill="var(--ink)"/>
    <polygon points="276,47 339,47 339,62 288,62" fill="var(--mid)"/>
    <g fill="var(--mid)"><polygon points="246,47 250,47 262,62 258,62"/><polygon points="254,47 258,47 270,62 266,62"/><polygon points="262,47 266,47 278,62 274,62"/></g>
  </svg>
  <div class="brand head-brand">Kestrel</div>
  <h2 class="page-title"><b>BUSINESS</b> <span>OVERVIEW</span></h2>
  <div class="copy">
    <p>Kestrel Dwellings Developments, is an emerging New Zealand property investment company with a focus on providing unique property investment opportunities.</p>
    <p>Our expertise and capabilities in architectural modular homes provide us with a remarkable advantage in tackling the development of properties that are typically considered challenging, remote, or uniquely positioned.</p>
    <p>As a company, with 48 employees boasting a wealth of experience in handling complex architectural projects, making us well-equipped to navigate the intricacies and demands of such ventures.</p>
    <p>This advantage allows us to not only execute projects efficiently but also to deliver exceptional results within condensed time frames.</p>
    <p>By capitalizing on our ability to develop difficult, remote, or one-of-a-kind properties swiftly and effectively, Kestrel Dwellings Developments offers investors a rare chance to engage in projects that promise exceptional profitability in the New Zealand property market.</p>
    <p>Our specialization in this niche sector of property development not only sets us apart from competitors, but also paves the way for lucrative investment opportunities in the New Zealand property market.</p>
  </div>
  <svg class="bracket" width="339" height="439"><polyline points="179,288 245,288 245,296" fill="none" stroke="var(--ink)" stroke-width="1"/><polyline points="95,380 95,388 160,388" fill="none" stroke="var(--ink)" stroke-width="1"/></svg>
  <div class="photo photo--villa" role="img" aria-label="Modern dark modular villa with lit interior and landscaped lawn at dusk"></div>
  <div class="photo photo--facade" role="img" aria-label="Two-storey black modular home facade with garage and garden"></div>
  <footer class="page-foot">
    <svg class="foot-svg" width="339" height="16"><rect width="339" height="16" fill="var(--ink)"/><polygon points="274,0 339,0 339,16 262,16" fill="var(--mid)"/><polygon points="270,0 274,0 262,16 258,16" fill="var(--paper)"/></svg>
    <div class="foot-item foot-item--phone"><span class="foot-icon"><svg width="6" height="6" viewBox="0 0 24 24"><path fill="#111" d="M6.6 10.8a15 15 0 006.6 6.6l2.2-2.2c.3-.3.7-.4 1-.2 1.1.4 2.3.6 3.6.6.6 0 1 .4 1 1V20c0 .6-.4 1-1 1A17 17 0 013 4c0-.6.4-1 1-1h3.5c.6 0 1 .4 1 1 0 1.3.2 2.5.6 3.6.1.3 0 .7-.2 1z"/></svg></span>09 555 0142</div>
    <div class="foot-item foot-item--mail"><span class="foot-icon"><svg width="6" height="6" viewBox="0 0 24 24"><path fill="#111" d="M3 5h18v14H3z"/><path fill="none" stroke="#fff" stroke-width="2" d="M3 6l9 7 9-7"/></svg></span>sales@kestreldwellings.co.nz</div>
    <div class="page-no">PAGE NO 02</div>
  </footer>
</section>

<!-- business origins -->
<section class="page page--origins">
  <svg class="page-head" width="339" height="62" viewBox="0 0 339 62">
    <rect width="339" height="54" fill="var(--soft)"/>
    <polygon points="104,0 112,0 158,54 150,54" fill="var(--light)"/>
    <polygon points="112,0 339,0 339,47 152,47" fill="var(--ink)"/>
    <polygon points="276,47 339,47 339,62 288,62" fill="var(--mid)"/>
    <g fill="var(--mid)"><polygon points="246,47 250,47 262,62 258,62"/><polygon points="254,47 258,47 270,62 266,62"/><polygon points="262,47 266,47 278,62 274,62"/></g>
  </svg>
  <div class="brand head-brand">Kestrel</div>
  <h2 class="page-title"><b>BUSINESS</b> <span>ORIGINS</span></h2>
  <div class="photo photo--meeting" role="img" aria-label="Business meeting at a desk with a small architectural building model and documents"></div>
  <div class="copy">
    <p>Kestrel Dwellings Developments was established with the goal of transforming the property investment market in New Zealand by introducing an innovative approach that centers on architectural modular designs and streamlined project timelines.</p>
    <p>Driven by our enthusiasm for architecture and real estate, we have expanded our successful business model to not only offer financial opportunities for investors but also to expand on our passion for high-end architectural design.</p>
    <p>With a wealth of experience accumulated over the past six years in the construction and the property market, we are pivoting to focus solely on our property development initiatives, presenting completed Kestrel projects to the market, in exclusive locations.</p>
    <p>These projects will boast high-quality standards, meticulous attention to detail and landscaping, and creative design elements.</p>
    <p>By introducing completed Kestrel properties into the market, we aim to reach a wider audience, catering to individuals who prefer ready-to-occupy homes, over engaging in the design and construction process. This approach also simplifies the financing process for prospective buyers, as established properties are often preferred by financial lenders.</p>
  </div>
  <footer class="page-foot">
    <svg class="foot-svg" width="339" height="16"><rect width="339" height="16" fill="var(--ink)"/><polygon points="274,0 339,0 339,16 262,16" fill="var(--mid)"/><polygon points="270,0 274,0 262,16 258,16" fill="var(--paper)"/></svg>
    <div class="foot-item foot-item--phone"><span class="foot-icon"><svg width="6" height="6" viewBox="0 0 24 24"><path fill="#111" d="M6.6 10.8a15 15 0 006.6 6.6l2.2-2.2c.3-.3.7-.4 1-.2 1.1.4 2.3.6 3.6.6.6 0 1 .4 1 1V20c0 .6-.4 1-1 1A17 17 0 013 4c0-.6.4-1 1-1h3.5c.6 0 1 .4 1 1 0 1.3.2 2.5.6 3.6.1.3 0 .7-.2 1z"/></svg></span>09 555 0142</div>
    <div class="foot-item foot-item--mail"><span class="foot-icon"><svg width="6" height="6" viewBox="0 0 24 24"><path fill="#111" d="M3 5h18v14H3z"/><path fill="none" stroke="#fff" stroke-width="2" d="M3 6l9 7 9-7"/></svg></span>sales@kestreldwellings.co.nz</div>
    <div class="page-no">PAGE NO 03</div>
  </footer>
</section>

</body>
</html>
```